Lantern Petals Website v.1 - attract floral shop franchisees

I need a simple information website for my new business. We are a franchisor of flower shops. The overall purpose of the website is to promote the company and the service, especially to potential franchisees and retailers. Only about 4 pages are required including homepage, About, For Supermarkets, For Franchisees, and Contact. No special functions are required except the site will have two separate inquiry forms that must be filled out online and submitted via automated email. Similarly, an email form should be linked from the Contact page. I have a logo and business cards designed by ArtMingle, and I would like the site to have a consistent color scheme and style. The key to design will be to express the joy and love associated with flowers and floral bouquets.
IMPORTANT - I will be exporting the website design to Wordpress CMS in a site hosted by HostNimbus. For smooth integration into WordPress hosted by HostNimbus, the designer should build the site using a WordPress-friendly format. Ideally, they should use HTML, CSS, and PHP. Creating a custom theme or using a page builder that exports to WordPress-compatible files is best. This ensures the site can be easily imported and managed within WordPress.

Target Market(s)

Potential franchisees (existing florists or creative types who might like to own a floral business) and supermarkets who might want us to run their floral department

Industry/Entity Type

Floral retailing

Requirements
Must have
• A brand theme that is beautiful, consistent throughout and builds on the logo design
Nice to have
• Show gender and ethnic diversity in customers and florists. Pictures of happy florists (for franchisees) and pictures of amazing floral department displays (for supermarkets)

```html
<!DOCTYPE html>
<html lang="en">
<head>
<meta charset="utf-8">
<title>Lantern Petals – Floral Franchising</title>
<link href="https://fonts.googleapis.com/css2?family=Great+Vibes&family=Montserrat:wght@400;500;600;700&family=Raleway:wght@400;500&display=swap" rel="stylesheet">
<style>
:root{
  --orange:#f2ae2e;
  --green:#059345;
  --green-dark:#04803b;
  --ink:#3a3a3a;
  --white:#ffffff;
  --blush:#fbeeea;
}
*{box-sizing:border-box;margin:0;padding:0}
html,body{width:1200px;height:3419px;overflow:hidden}
body{position:relative;background:var(--white);font-family:"Raleway",sans-serif;color:var(--ink)}
.abs{position:absolute}
.script{font-family:"Great Vibes",cursive;font-weight:400}
.sans{font-family:"Montserrat",sans-serif}

/* header */
.topbar-item{position:absolute;top:14px;display:flex;align-items:center;gap:14px;font-family:"Montserrat",sans-serif;font-weight:500;font-size:19px;color:#222}
.hex{width:56px;height:60px;display:block}
.navband{position:absolute;left:0;top:88px;width:1200px;height:73px;background:var(--orange)}
.nav a{position:absolute;top:119px;color:var(--white);font-family:"Montserrat",sans-serif;font-size:15px;font-weight:500;text-decoration:none}
.logo-tab{position:absolute;left:126px;top:78px;width:320px;height:120px;background:var(--white);border-radius:0 0 40px 40px;display:flex;align-items:center;justify-content:center;gap:10px;z-index:3}
.logo-dot{width:16px;height:16px;border-radius:50%;background:var(--orange)}
.logo-name{font-family:"Montserrat",sans-serif;font-weight:600;font-size:26px;color:var(--orange)}

/* hero */
.hero{position:absolute;left:0;top:161px;width:1200px;height:640px;background:linear-gradient(100deg,#a9b7a4 0%,#d8cfbf 35%,#c3c9c6 60%,#8f9a9a 100%)}
.hero-text{position:absolute;left:0;top:365px;width:1200px;text-align:center;color:var(--white);z-index:2}
.hero-title{font-size:60px;line-height:1}
.hero-sub{font-family:"Montserrat",sans-serif;font-size:31px;letter-spacing:9px;margin-top:8px}
.hero-tag{font-family:"Montserrat",sans-serif;font-size:19px;font-weight:500;margin-top:14px}
.btn{display:inline-block;border-radius:24px;font-family:"Montserrat",sans-serif;font-weight:600;font-size:16px;text-decoration:none;text-align:center}
.btn-light{background:var(--white);color:var(--green);padding:13px 24px}
.btn-green{background:var(--green);color:var(--white);padding:12px 27px}
.btn-outline{border:2px solid var(--white);color:var(--white);padding:11px 27px}

/* feature sections */
.photo-circle{position:absolute;width:414px;height:414px;border-radius:50%}
.section-title{position:absolute;font-size:52px;color:var(--orange);line-height:1}
.rule{position:absolute;height:3px;width:70px;background:var(--green)}
.copy{position:absolute;font-size:16.5px;line-height:26px;color:#333}

.about{position:absolute;left:0;top:1363px;width:600px;height:545px;background:var(--green)}
.about-photo{position:absolute;left:600px;top:1363px;width:600px;height:545px;background:linear-gradient(180deg,#6e7b6a,#3b4038 60%,#6a6457)}

/* inquiry */
.doubts{position:absolute;left:0;top:2570px;width:1200px;height:440px;background:linear-gradient(90deg,#fbe6e4,#fdf3ea 50%,#fbe5e3)}
.doubts h2{position:absolute;top:2660px;left:0;width:1200px;text-align:center;font-family:"Montserrat",sans-serif;font-weight:600;font-size:30px;color:var(--green)}

/* footer */
.footer{position:absolute;left:0;top:2980px;width:1200px;height:439px;background:var(--green)}
.foot-title{position:absolute;font-size:36px;color:var(--white)}
.foot-links a{position:absolute;left:174px;color:var(--white);font-size:16px;text-decoration:none;font-family:"Raleway",sans-serif}
.vdash{position:absolute;width:0;border-left:2px dashed rgba(255,255,255,.8)}
.contact-row{position:absolute;left:786px;display:flex;align-items:center;gap:16px;color:var(--white);font-size:17px;line-height:26px}
.foot-rule{position:absolute;left:103px;top:3361px;width:992px;height:1px;background:rgba(255,255,255,.6)}
.copyright{position:absolute;top:3381px;left:0;width:1200px;text-align:center;color:var(--white);font-size:15px}
</style>
</head>
<body>

<!-- header -->
<div class="topbar-item" style="left:548px">
  <svg class="hex" viewBox="0 0 56 60"><polygon points="28,0 54,15 54,45 28,60 2,45 2,15" fill="var(--orange)"/><path d="M20 19c2-1 4 0 5 2l2 4c0 2-1 3-2 3 1 3 3 5 6 6 0-1 1-2 3-2l4 2c2 1 2 3 1 5-2 3-6 3-9 1-5-3-9-7-11-12-1-3-1-7 1-9z" fill="#fff"/></svg>
  <span>+.614.555.0182</span>
</div>
<div class="topbar-item" style="left:790px">
  <svg class="hex" viewBox="0 0 56 60"><polygon points="28,0 54,15 54,45 28,60 2,45 2,15" fill="var(--orange)"/><rect x="16" y="21" width="24" height="17" rx="2" fill="#fff"/><path d="M16 22l12 9 12-9" stroke="var(--orange)" stroke-width="2" fill="none"/></svg>
  <span>hello@lanternpetals.example</span>
</div>

<div class="navband"></div>
<div class="logo-tab"><span class="logo-dot"></span><span class="logo-name">Lantern Petals</span></div>
<nav class="nav">
  <a style="left:536px">About Us</a>
  <a style="left:663px">For Supermarkets</a>
  <a style="left:835px">For Franchisees</a>
  <a style="left:1008px">Contact</a>
</nav>

<!-- hero -->
<div class="hero" role="img" aria-label="Florist handing a bouquet to a smiling customer across a flower shop counter"></div>
<svg class="abs" style="left:0;top:640px;z-index:1" width="1200" height="170" viewBox="0 0 1200 170">
  <path d="M0 60 C120 20 260 20 470 70 C700 125 900 170 1200 60 L1200 170 L0 170 Z" fill="#fff"/>
  <path d="M50 50 C200 10 350 20 520 75 C700 130 900 160 1140 100 C930 175 700 150 500 95 C340 50 200 30 50 50 Z" fill="var(--orange)"/>
</svg>
<div class="hero-text">
  <div class="hero-title script">Welcome To Lantern</div>
  <div class="hero-sub">PETALS</div>
  <div class="hero-tag">Freshest Flowers · Artisan Designs · Franchise Opportunities</div>
  <a class="btn btn-light" style="margin-top:26px">GET STARTED</a>
</div>

<!-- supermarkets -->
<div class="photo-circle" style="left:121px;top:855px;background:radial-gradient(circle at 45% 45%,#d7c6cc,#7d8a80 70%,#5a625c)" role="img" aria-label="Shopper choosing flowers from a supermarket floral display"></div>
<div class="section-title script" style="left:618px;top:870px">Supermarkets</div>
<div class="rule" style="left:620px;top:937px"></div>
<p class="copy" style="left:619px;top:964px;width:450px">Lantern Petals works with some of the country’s largest and most progressive supermarkets to provide franchisee ownership and operation of their strategically important floral departments. Supermarkets find that Lantern Petals is able to improve their financial outcomes, provide attentive customer service and satisfaction, and lift the quality of the entire store environment.</p>
<a class="btn btn-green abs" style="left:621px;top:1158px">READ MORE</a>
<div class="abs" style="left:860px;top:1125px;width:340px;height:235px;border-radius:50% 0 0 40%;background:radial-gradient(ellipse at 60% 55%,#f1a65a,#e9d8c8 55%,rgba(255,255,255,0) 75%)" role="img" aria-label="Loose bouquet of orange, purple and dried wildflowers"></div>

<!-- about -->
<div class="about">
  <div class="script abs" style="left:102px;top:114px;font-size:46px;color:#fff;line-height:1">About Lantern</div>
  <div class="sans abs" style="left:103px;top:170px;font-size:28px;font-weight:700;color:#fff">PETALS</div>
  <div class="abs" style="left:104px;top:212px;width:70px;height:3px;background:#fff"></div>
  <p class="abs" style="left:106px;top:236px;width:450px;font-size:16.5px;line-height:27px;color:#fff">Fresh flowers convey beauty and love, and in our view should become something every person regularly enjoys. Lantern Petals is an entrepreneurial company created to make top quality fresh flowers and professionally-designed bouquets accessible to every consumer at affordable prices.</p>
  <a class="btn btn-outline abs" style="left:106px;top:418px">READ MORE</a>
</div>
<div class="about-photo" role="img" aria-label="Florist holding tulips in the doorway of a plant-filled shop"></div>

<!-- franchisees -->
<div class="photo-circle" style="left:102px;top:2056px;background:radial-gradient(circle at 50% 60%,#e58aa0,#b9865c 55%,#5b4a3d)" role="img" aria-label="Colourful flower stall with buckets of blooms"></div>
<div class="abs" style="left:0;top:2335px;width:305px;height:235px;border-radius:0 50% 50% 0;background:radial-gradient(ellipse at 35% 50%,#f0a257,#e6c7cf 55%,rgba(255,255,255,0) 75%)" role="img" aria-label="Bouquet of orange, pink and purple wildflowers"></div>
<div class="section-title script" style="left:618px;top:2095px">Franchisees</div>
<div class="rule" style="left:620px;top:2164px"></div>
<p class="copy" style="left:619px;top:2190px;width:450px">Lantern Petals brings the best of professional florists and supermarkets together for the benefit of consumers. It supports a national network of owner-operator franchisees, who in many cases are multi-site professional florists, with comprehensive services to enhance franchise profitability.</p>
<a class="btn btn-green abs" style="left:621px;top:2342px">READ MORE</a>

<!-- inquiry -->
<div class="doubts" role="img" aria-label="Soft pink watercolour petals background"></div>
<h2 class="doubts" style="background:none;height:auto;top:2666px"></h2>
<div class="abs sans" style="left:0;top:2666px;width:1200px;text-align:center;font-weight:600;font-size:30px;color:var(--green)">Do You Have Any Doubts?</div>
<div class="abs" style="left:565px;top:2730px;width:70px;height:3px;background:var(--green)"></div>
<a class="btn btn-green abs" style="left:210px;top:2770px;width:348px;padding:13px 0;font-size:15.5px">NEW FLORIST FRANCHISE INQUIRY</a>
<a class="btn abs" style="left:577px;top:2770px;width:413px;padding:13px 0;background:#fff;color:#111;font-size:15.5px">PROFESSIONAL FLORIST FRANCHISE INQUIRY</a>

<!-- footer -->
<svg class="abs" style="left:0;top:2880px" width="1200" height="110" viewBox="0 0 1200 110">
  <path d="M0 110 L0 108 C250 40 520 20 760 15 C950 15 1100 40 1200 75 L1200 110 Z" fill="var(--green)"/>
  <path d="M50 108 C280 45 520 25 760 20 C960 18 1110 50 1200 75 L1200 62 C1100 30 950 5 760 5 C520 8 280 40 50 108 Z" fill="var(--orange)"/>
</svg>
<div class="footer"></div>
<div class="foot-title script" style="left:174px;top:3090px">Quick Links</div>
<div class="foot-links">
  <a style="top:3150px">About Us</a>
  <a style="top:3182px">For Supermarkets</a>
  <a style="top:3214px">For Franchisees</a>
  <a style="top:3246px">Contact</a>
</div>
<div class="vdash" style="left:342px;top:3079px;height:232px"></div>
<div class="abs" style="left:344px;top:3165px;width:395px;display:flex;justify-content:center;align-items:center;gap:12px">
  <span style="width:18px;height:18px;border-radius:50%;background:#fff"></span>
  <span class="sans" style="font-weight:600;font-size:34px;color:#fff">Lantern Petals</span>
</div>
<div class="vdash" style="left:739px;top:3079px;height:232px"></div>
<div class="foot-title script" style="left:801px;top:3030px">Contact Us</div>
<div class="contact-row" style="top:3094px">
  <svg class="hex" viewBox="0 0 56 60"><polygon points="28,0 54,15 54,45 28,60 2,45 2,15" fill="var(--orange)"/><circle cx="28" cy="24" r="6" fill="#fff"/><path d="M17 41c0-7 5-10 11-10s11 3 11 10z" fill="#fff"/></svg>
  <span>Miriam T. Osei<br>Founder and CEO</span>
</div>
<div class="contact-row" style="top:3179px">
  <svg class="hex" viewBox="0 0 56 60"><polygon points="28,0 54,15 54,45 28,60 2,45 2,15" fill="var(--orange)"/><path d="M20 19c2-1 4 0 5 2l2 4c0 2-1 3-2 3 1 3 3 5 6 6 0-1 1-2 3-2l4 2c2 1 2 3 1 5-2 3-6 3-9 1-5-3-9-7-11-12-1-3-1-7 1-9z" fill="#fff"/></svg>
  <span>+.614.555.0182</span>
</div>
<div class="contact-row" style="top:3258px">
  <svg class="hex" viewBox="0 0 56 60"><polygon points="28,0 54,15 54,45 28,60 2,45 2,15" fill="var(--orange)"/><rect x="16" y="21" width="24" height="17" rx="2" fill="#fff"/><path d="M16 22l12 9 12-9" stroke="var(--orange)" stroke-width="2" fill="none"/></svg>
  <span>hello@lanternpetals.example</span>
</div>
<div class="foot-rule"></div>
<div class="copyright">© 2024 Lantern Petals &nbsp;|&nbsp; All rights reserved &nbsp;|&nbsp; Privacy &nbsp;|&nbsp; Terms of Use</div>

</body>
</html>
```